Bramblewick Forage Business Cards

I need a business card with my logo, number, Facebook account, and some information about what I am selling. Green card with logo on the front. 555-214-8392 phone number, @bramblewickforage Facebook, •Orchardgrass Hay •Alfalfa Hay •Mixed Grass Hay , and “Premium Quality Hay” all written on the back.

Target Market(s)

Hay

Contact Information for Business Card

Phone number, Facebook, different types of hay.

Colors
00AB8E
00BBA5
67D7C9
C6EFE9
E9F9F6

```html
<!DOCTYPE html>
<html lang="en">
<head>
<meta charset="utf-8">
<title>Bramblewick Forage Business Cards</title>
<link href="https://fonts.googleapis.com/css2?family=Roboto:wght@400;500;700&display=swap" rel="stylesheet">
<style>
  :root {
    --backdrop: #2b2b2b;
    --card: #ffffff;
    --leaf-green: #00a651;
    --band-dark: #333333;
    --ink: #111111;
    --on-band: #ffffff;
  }
  * { margin: 0; padding: 0; box-sizing: border-box; }
  html, body {
    width: 1200px;
    height: 1108px;
    overflow: hidden;
    background: var(--backdrop);
    font-family: "Roboto", sans-serif;
  }
  .canvas {
    position: relative;
    width: 1200px;
    height: 1108px;
    display: flex;
    justify-content: center;
    align-items: center;
    gap: 80px;
  }
  .card {
    position: relative;
    width: 400px;
    height: 700px;
    background: var(--card);
    border-radius: 24px;
    overflow: hidden;
    box-shadow: 0 14px 30px rgba(0,0,0,0.45);
  }
  /* Front */
  .front-brand {
    position: absolute;
    top: 250px;
    left: 0;
    width: 100%;
    display: flex;
    flex-direction: column;
    align-items: center;
    gap: 16px;
  }
  .brand-line {
    display: flex;
    align-items: center;
    gap: 12px;
  }
  .brand-dot {
    width: 34px;
    height: 34px;
    border-radius: 50%;
    background: var(--leaf-green);
  }
  .brand-name {
    font-weight: 700;
    font-size: 28px;
    color: var(--ink);
  }
  .front-phone {
    font-weight: 700;
    font-size: 30px;
    color: var(--ink);
    letter-spacing: 0.5px;
  }
  .product-band {
    position: absolute;
    top: 470px;
    left: 0;
    width: 100%;
    height: 96px;
    background: var(--leaf-green);
    color: var(--on-band);
    display: flex;
    flex-direction: column;
    justify-content: center;
    align-items: center;
    font-size: 17px;
    line-height: 1.45;
    text-align: center;
  }
  /* Back */
  .back-brand {
    position: absolute;
    top: 200px;
    left: 0;
    width: 100%;
    display: flex;
    flex-direction: column;
    align-items: center;
    gap: 22px;
  }
  .back-dot {
    width: 90px;
    height: 90px;
    border-radius: 50%;
    background: var(--leaf-green);
  }
  .back-name {
    font-weight: 700;
    font-size: 36px;
    color: var(--ink);
    text-align: center;
    line-height: 1.15;
  }
  .contact-band {
    position: absolute;
    top: 478px;
    left: 0;
    width: 100%;
    height: 110px;
    background: var(--band-dark);
    color: var(--on-band);
    display: flex;
    flex-direction: column;
    justify-content: center;
    align-items: center;
    gap: 6px;
  }
  .contact-phone {
    font-weight: 500;
    font-size: 38px;
    letter-spacing: 0.5px;
  }
  .contact-social {
    display: flex;
    align-items: center;
    gap: 8px;
    font-size: 22px;
  }
  .social-dot {
    width: 22px;
    height: 22px;
    border-radius: 50%;
    background: var(--on-band);
  }
</style>
</head>
<body>
  <main class="canvas">
    <section class="card card-front">
      <div class="front-brand">
        <div class="brand-line">
          <span class="brand-dot"></span>
          <span class="brand-name">Bramblewick Forage</span>
        </div>
        <div class="front-phone">555-214-8392</div>
      </div>
      <div class="product-band">
        <span>Orchardgrass Hay • Alfalfa Hay</span>
        <span>Mixed Grass Hay, &amp; Premium Quality Hay</span>
      </div>
    </section>

    <section class="card card-back">
      <div class="back-brand">
        <span class="back-dot"></span>
        <span class="back-name">Bramblewick<br>Forage</span>
      </div>
      <div class="contact-band">
        <div class="contact-phone">555-214-8392</div>
        <div class="contact-social">
          <span class="social-dot"></span>
          <span>@bramblewickforage</span>
        </div>
      </div>
    </section>
  </main>
</body>
</html>
```